Business card for a new cabinet shop company named Veloran Cabinets for high end cabinets

Design a business card, thinking dark rich green with colours to speak of high end luxury ie; cream, gold, black possibly

Mitchell Tarrowby
Director Craftsman
Email: info@veloranjoinery-example.com.au
Instagram : @veloran.cabinets

```html
<!DOCTYPE html>
<html lang="en">
<head>
<meta charset="utf-8">
<title>Veloran Cabinets – Business Card</title>
<link rel="stylesheet" href="https://fonts.googleapis.com/css2?family=Barlow:wght@400;500;600;700&display=swap">
<style>
  :root {
    --backdrop: #1c1c1c;
    --card-green-deep: #050c07;
    --card-green: #0b2314;
    --gold: #c9a95c;
    --gold-edge: #b89545;
    --cream: #d9d2bf;
    --muted: #a7a79f;
  }
  * { margin: 0; padding: 0; box-sizing: border-box; }
  html, body {
    width: 1200px; height: 875px; overflow: hidden;
    background: var(--backdrop);
    font-family: "Barlow", sans-serif;
  }
  .canvas {
    width: 1200px; height: 875px;
    display: flex; flex-direction: column;
    align-items: center; justify-content: center; gap: 35px;
  }
  .card {
    position: relative;
    width: 700px; height: 400px;
    border-radius: 24px;
    border: 1.5px solid var(--gold-edge);
    background: linear-gradient(200deg, var(--card-green) 0%, var(--card-green-deep) 70%);
    box-shadow: 0 18px 40px rgba(0,0,0,.55);
    overflow: hidden;
  }
  /* Front */
  .card-front {
    display: flex; align-items: center; justify-content: center; gap: 22px;
  }
  .brand-mark {
    width: 62px; height: 62px;
    border: 3px solid var(--gold);
    border-radius: 4px;
  }
  .brand-name {
    color: var(--gold);
    font-weight: 500;
    font-size: 52px;
    letter-spacing: 1px;
  }
  /* Back */
  .card-back { padding: 70px 60px; }
  .back-brand {
    display: flex; align-items: center; gap: 14px;
  }
  .back-brand .brand-mark { width: 36px; height: 36px; border-width: 2px; }
  .back-brand .brand-name { font-size: 30px; }
  .person { margin-top: 58px; }
  .person-name {
    color: var(--gold);
    font-weight: 700;
    font-size: 30px;
    letter-spacing: .5px;
    text-transform: uppercase;
  }
  .person-role {
    color: var(--muted);
    font-size: 19px;
    margin-top: 2px;
  }
  .contact-list { list-style: none; margin-top: 26px; }
  .contact-item {
    display: flex; align-items: center; gap: 12px;
    color: var(--cream);
    font-size: 16px;
    line-height: 26px;
  }
  .contact-icon { width: 16px; height: 16px; flex: none; }
</style>
</head>
<body>
<main class="canvas">
  <section class="card card-front" aria-label="Card front">
    <span class="brand-mark" aria-hidden="true"></span>
    <span class="brand-name">Veloran Cabinets</span>
  </section>

  <section class="card card-back" aria-label="Card back">
    <div class="back-brand">
      <span class="brand-mark" aria-hidden="true"></span>
      <span class="brand-name">Veloran Cabinets</span>
    </div>
    <div class="person">
      <h1 class="person-name">Mitchell Tarrowby</h1>
      <p class="person-role">Director Craftsman</p>
    </div>
    <ul class="contact-list">
      <li class="contact-item">
        <svg class="contact-icon" viewBox="0 0 16 16" aria-hidden="true">
          <path d="M8 1a5 5 0 0 0-5 5c0 4 5 9 5 9s5-5 5-9a5 5 0 0 0-5-5z" fill="#c9a95c"/>
          <circle cx="8" cy="6" r="2" fill="#07140b"/>
        </svg>
        Western Australia
      </li>
      <li class="contact-item">
        <svg class="contact-icon" viewBox="0 0 16 16" aria-hidden="true">
          <rect x="1" y="3" width="14" height="10" rx="1" fill="#c9a95c"/>
          <path d="M1.5 3.5 8 9l6.5-5.5" fill="none" stroke="#07140b" stroke-width="1.3"/>
        </svg>
        info@veloranjoinery-example.com.au
      </li>
      <li class="contact-item">
        <svg class="contact-icon" viewBox="0 0 16 16" aria-hidden="true">
          <circle cx="8" cy="8" r="6.5" fill="none" stroke="#c9a95c" stroke-width="1.6"/>
        </svg>
        @veloran.cabinets
      </li>
    </ul>
  </section>
</main>
</body>
</html>
```